Our companies name is The Gilded Ladle and we specialize in craft cupcakes, what I mean by that is that we bake our cupcakes with craft beer and other alcoholic drinks. We are trying to focus on being elegant but at the same time unpretentious. Since we are incorporating beer in our cupcakes we want the business card to have our logo in the front and our information in the back.

Once we select the best design we will provide the contact information to be added. Thank you.

Industry/Entity Type

Business

Font styles to use
Decorative
Script

Requirements
Must have
• Round corners
Should not have
• Square corners

```html
<!DOCTYPE html>
<html lang="en">
<head>
<meta charset="utf-8">
<title>The Gilded Ladle – Business Card</title>
<link rel="stylesheet" href="https://fonts.googleapis.com/css2?family=Exo+2:wght@400;500;600&display=swap">
<style>
  :root {
    --backdrop: #e4e6ec;
    --card-white: #f4f4f4;
    --card-black: #0a0a0a;
    --accent-orange: #f05a22;
    --text-light: #ffffff;
    --brand-ink: #1c1c1c;
    --brand-dot: #e8323c;
  }
  * { box-sizing: border-box; margin: 0; padding: 0; }
  html, body {
    width: 1200px; height: 840px; overflow: hidden;
    background: var(--backdrop);
    font-family: "Exo 2", sans-serif;
  }
  .stage {
    width: 1200px; height: 840px;
    display: flex; align-items: center; justify-content: center;
  }
  .business-card {
    position: relative;
    width: 1050px; height: 600px;
    border-radius: 28px;
    overflow: hidden;
    background: var(--card-white);
    box-shadow: 0 12px 40px rgba(0,0,0,0.18);
  }
  .card-shapes { position: absolute; inset: 0; }
  .brand {
    position: absolute;
    left: 70px; top: 250px;
    display: flex; align-items: center; gap: 16px;
  }
  .brand-dot {
    width: 34px; height: 34px; border-radius: 50%;
    background: var(--brand-dot);
  }
  .brand-name {
    font-size: 40px; font-weight: 600;
    color: var(--brand-ink);
    letter-spacing: 0.5px;
  }
  .contact-block {
    position: absolute;
    right: 60px; top: 70px;
    text-align: right;
    color: var(--text-light);
  }
  .person-name { font-size: 28px; font-weight: 500; letter-spacing: 1px; }
  .person-title { font-size: 17px; letter-spacing: 1px; margin-top: 2px; }
  .address { font-size: 21px; line-height: 1.3; margin-top: 50px; }
  .contact-list { list-style: none; margin-top: 40px; }
  .contact-list li {
    display: flex; justify-content: flex-end; align-items: center;
    gap: 14px; font-size: 21px; height: 40px;
  }
  .contact-list li.web { padding-right: 38px; }
  .contact-icon { width: 24px; height: 24px; fill: none; stroke: var(--text-light); stroke-width: 2; }
  .contact-icon .solid { fill: var(--text-light); stroke: none; }
</style>
</head>
<body>
<main class="stage">
  <article class="business-card">
    <svg class="card-shapes" viewBox="0 0 1050 600" preserveAspectRatio="none" aria-hidden="true">
      <path d="M682,0 L1050,0 L1050,600 L0,600 L0,488 C370,458 620,270 682,0 Z" fill="var(--accent-orange)"/>
      <path d="M698,0 L1050,0 L1050,600 L0,600 L0,506 C380,476 636,282 698,0 Z" fill="var(--card-black)"/>
    </svg>

    <div class="brand">
      <span class="brand-dot"></span>
      <span class="brand-name">The Gilded Ladle</span>
    </div>

    <div class="contact-block">
      <p class="person-name">DANA OKAFOR</p>
      <p class="person-title">PRESIDENT</p>
      <p class="address">12 Copper Kettle Lane<br>Harbour Row BRK</p>
      <ul class="contact-list">
        <li>021 555 0147
          <svg class="contact-icon" viewBox="0 0 24 24"><path class="solid" d="M6.6 10.8a15 15 0 0 0 6.6 6.6l2.2-2.2a1 1 0 0 1 1-.25 11 11 0 0 0 3.6.6 1 1 0 0 1 1 1V20a1 1 0 0 1-1 1A17 17 0 0 1 3 4a1 1 0 0 1 1-1h3.5a1 1 0 0 1 1 1 11 11 0 0 0 .6 3.6 1 1 0 0 1-.25 1z"/></svg>
        </li>
        <li>021 555 0148
          <svg class="contact-icon" viewBox="0 0 24 24"><rect x="7" y="2" width="10" height="20" rx="2"/><line x1="11" y1="18" x2="13" y2="18"/></svg>
        </li>
        <li>021 555 0149
          <svg class="contact-icon" viewBox="0 0 24 24"><rect x="4" y="8" width="16" height="13"/><rect x="8" y="3" width="8" height="5"/><line x1="8" y1="12" x2="16" y2="12"/><line x1="8" y1="16" x2="16" y2="16"/></svg>
        </li>
        <li>hello@gildedladle.com
          <svg class="contact-icon" viewBox="0 0 24 24"><rect x="3" y="5" width="18" height="14"/><polyline points="3,5 12,13 21,5"/></svg>
        </li>
        <li>www.gildedladle.com
          <svg class="contact-icon" viewBox="0 0 24 24"><circle cx="12" cy="12" r="9"/><ellipse cx="12" cy="12" rx="4" ry="9"/><line x1="3" y1="12" x2="21" y2="12"/></svg>
        </li>
      </ul>
    </div>
  </article>
</main>
</body>
</html>
```